Business Card Design Project

I need a business card designed from scratch. I have an existing logo that I can upload in Illustrator for modification or redesign.

The Company is called Query Lanterns http://querylanterns.com.au and we provide Search Engine Optimization services to Australian businesses. The current logo signifies an increase in visitors, profits etc...

There are no restrictions as to the redesign - colours, style etc are all open to change.

Cards will be full colour and one sided printed at http://www.cardmoxel.com.au so check their requirements for file format and sizes etc.

I will expect all original files upon completion of project.

Target Market(s)

Any business with a web site looking to improve their search engine rankings

Industry/Entity Type

Business

Requirements
Must have
• I like modern, sleek designs. Clean, not fussy, uncluttered.

```html
<!DOCTYPE html>
<html lang="en">
<head>
<meta charset="utf-8">
<title>Query Lanterns – Business Card</title>
<link rel="stylesheet" href="https://fonts.googleapis.com/css2?family=Josefin+Sans:wght@400;600;700&display=swap">
<style>
  :root {
    --page-bg: #e9ecef;
    --card-blue: #3ba4d8;
    --ink-navy: #1e4c86;
    --ink-light: #eaf5fb;
    --ink-soft: #d5e9f4;
    --icon-navy: #1f4a80;
  }
  * { margin: 0; padding: 0; box-sizing: border-box; }
  html, body {
    width: 1200px;
    height: 900px;
    overflow: hidden;
    background: var(--page-bg);
    font-family: "Josefin Sans", sans-serif;
  }
  .card {
    position: absolute;
    left: 120px;
    top: 156px;
    width: 960px;
    height: 588px;
    background: var(--card-blue);
    border-radius: 4px;
    box-shadow: 0 6px 20px rgba(0, 0, 0, 0.12);
    overflow: hidden;
  }
  .brand {
    position: absolute;
    left: 64px;
    top: 70px;
    display: flex;
    align-items: center;
    gap: 22px;
  }
  .brand-dot {
    width: 58px;
    height: 58px;
    border-radius: 50%;
    background: var(--ink-navy);
  }
  .brand-name {
    font-size: 64px;
    font-weight: 700;
    color: var(--ink-navy);
    letter-spacing: 0.5px;
    line-height: 1;
    padding-top: 8px;
  }
  .person {
    position: absolute;
    left: 64px;
    top: 280px;
  }
  .person-name {
    font-size: 40px;
    font-weight: 700;
    color: var(--ink-navy);
    line-height: 1.1;
  }
  .person-role {
    font-size: 40px;
    font-weight: 400;
    color: var(--ink-soft);
    margin-top: 8px;
    line-height: 1.1;
  }
  .contact-list {
    position: absolute;
    list-style: none;
    color: var(--ink-light);
    font-size: 30px;
    font-weight: 400;
  }
  .contact-list li {
    display: flex;
    align-items: center;
    gap: 16px;
    line-height: 1;
    white-space: nowrap;
  }
  .contact-list--phones { left: 64px; top: 430px; }
  .contact-list--phones li + li { margin-top: 28px; }
  .contact-list--web {
    right: 72px;
    top: 325px;
    font-size: 24px;
  }
  .contact-list--web li + li { margin-top: 24px; }
  .contact-icon {
    width: 22px;
    height: 22px;
    flex: none;
    fill: var(--icon-navy);
  }
  .contact-list--web .contact-icon { width: 20px; height: 20px; }
</style>
</head>
<body>
  <main class="card">
    <div class="brand">
      <span class="brand-dot"></span>
      <span class="brand-name">Query Lanterns</span>
    </div>

    <div class="person">
      <p class="person-name">Daniel Reeve</p>
      <p class="person-role">Director</p>
    </div>

    <ul class="contact-list contact-list--phones">
      <li>
        <svg class="contact-icon" viewBox="0 0 24 24" aria-hidden="true">
          <path d="M6.6 2.5c.6-.3 1.3 0 1.6.6l1.5 3.4c.2.5.1 1.1-.3 1.5L8 9.4c.9 2.3 2.4 4.2 4.5 5.6l1.5-1.3c.4-.4 1-.5 1.5-.2l3.3 1.7c.6.3.8 1 .5 1.6l-1.2 2.4c-.4.8-1.3 1.2-2.1 1-6.3-1.7-10.6-6.700-11.6-13-.1-.9.3-1.7 1.1-2.1z"/>
        </svg>
        1300 482915
      </li>
      <li>
        <svg class="contact-icon" viewBox="0 0 24 24" aria-hidden="true">
          <path d="M8 1h2v3h5a2 2 0 0 1 2 2v14a2 2 0 0 1-2 2H9a2 2 0 0 1-2-2V6c0-.6.3-1.1.7-1.5H8zM9.5 7v5h5V7zm0 7v1.6h1.5V14zm3.5 0v1.6h1.5V14zm-3.5 3v1.6h1.5V17zm3.5 0v1.6h1.5V17z"/>
        </svg>
        + 61 (0)2 9471 3620
      </li>
    </ul>

    <ul class="contact-list contact-list--web">
      <li>
        <svg class="contact-icon" viewBox="0 0 24 24" aria-hidden="true">
          <path d="M2 5h20v14H2zm2 2v.4l8 5.3 8-5.3V7zm0 2.8V17h16V9.8l-8 5.3z"/>
        </svg>
        enquiry@querylanterns.com.au
      </li>
      <li>
        <svg class="contact-icon" viewBox="0 0 24 24" aria-hidden="true">
          <path d="M12 2a10 10 0 1 0 0 20 10 10 0 0 0 0-20zm6.9 9h-3a15 15 0 0 0-1.3-5.6A8 8 0 0 1 18.9 11zM12 4.1c.9 1.2 1.7 3.6 1.9 6.9h-3.8c.2-3.3 1-5.7 1.9-6.9zM9.4 5.4A15 15 0 0 0 8.1 11h-3a8 8 0 0 1 4.3-5.6zM5.1 13h3a15 15 0 0 0 1.3 5.6A8 8 0 0 1 5.1 13zm6.9 6.9c-.9-1.2-1.7-3.6-1.9-6.9h3.8c-.2 3.3-1 5.7-1.9 6.9zm2.6-1.3a15 15 0 0 0 1.3-5.6h3a8 8 0 0 1-4.3 5.6z"/>
        </svg>
        www.querylanterns.com.au
      </li>
    </ul>
  </main>
</body>
</html>
```